Redesign of Medical App for Patients

• The Designer’s task is to provide a new fully-responsive design for our apps, and then code it using only basic html and CSS.
• Your design will be incorporated into our existing REACT native app.

Target Market(s)

Medical Patients

Industry/Entity Type

Medical

Coding

Coded - Design and coding required

Number of Pages Required

5+ page

Requirements
Must have
• Short list candidates will receive detailed briefing
Nice to have
• detailed briefing contains some of our ideas.

```html
<!DOCTYPE html>
<html lang="en">
<head>
<meta charset="utf-8">
<title>CareSteps – Patient App Screens</title>
<link rel="stylesheet" href="https://fonts.googleapis.com/css2?family=Saira+Semi+Condensed:wght@500;600&family=Open+Sans:wght@400;600&display=swap">
<style>
  :root {
    --page: #ebe7e2;
    --brand: #2f86b8;
    --brand-deep: #1f6b98;
    --brand-soft: #5aa6d2;
    --ink: #1c2530;
    --ink-soft: #3d4853;
    --muted: #9aa4ad;
    --card: #ffffff;
    --screen-tint: #f2f4f6;
    --line: #e3e7eb;
    --display: "Saira Semi Condensed", "Arial Narrow", sans-serif;
  }
  * { box-sizing: border-box; margin: 0; padding: 0; }
  html, body { width: 1200px; height: 780px; overflow: hidden; }
  body {
    background: var(--page);
    font-family: "Open Sans", Arial, sans-serif;
    color: var(--ink);
    position: relative;
  }
  .screen {
    position: absolute;
    top: 30px;
    width: 340px;
    height: 720px;
    border-radius: 28px;
    overflow: hidden;
    background: var(--card);
    box-shadow: 0 10px 30px rgba(40, 40, 40, 0.12);
    display: flex;
    flex-direction: column;
  }
  .screen--about { left: 50px; }
  .screen--pre { left: 430px; background: var(--screen-tint); }
  .screen--recovery { left: 810px; background: var(--screen-tint); }

  .brand {
    display: flex;
    align-items: center;
    justify-content: center;
    gap: 8px;
    padding-top: 26px;
    font-family: var(--display);
    font-weight: 600;
    font-size: 26px;
    letter-spacing: 0.2px;
    color: var(--brand);
    flex-shrink: 0;
  }
  .brand__dot {
    width: 24px; height: 24px; border-radius: 50%;
    background: var(--brand);
  }
  .brand--light { color: #ffffff; }
  .brand--light .brand__dot { background: #ffffff; }

  .section-title {
    font-family: var(--display);
    font-weight: 600;
    font-size: 23px;
    text-transform: uppercase;
    flex-shrink: 0;
  }

  /* About screen */
  .screen--about .brand { padding-top: 22px; }
  .screen--about .section-title { padding: 10px 20px 8px; color: var(--ink); }
  .topic-list {
    flex: 1 1 auto; min-height: 0; overflow: hidden;
    padding: 2px 12px; display: flex; flex-direction: column; gap: 8px;
  }
  .topic {
    display: flex; gap: 10px;
    background: var(--card);
    border-radius: 12px;
    padding: 7px 8px;
    box-shadow: 0 2px 10px rgba(30, 60, 90, 0.10);
  }
  .topic__photo {
    flex: 0 0 92px; align-self: stretch; min-height: 100px; border-radius: 6px;
    background: linear-gradient(135deg, #c9d7e0, #8fb0c4 55%, #e6e3de);
  }
  .topic__body { flex: 1; }
  .topic__title {
    font-family: var(--display);
    font-weight: 500; font-size: 13.5px; line-height: 1.3;
    text-transform: uppercase; margin-bottom: 3px;
  }
  .topic__text { font-size: 10px; line-height: 1.45; color: var(--ink-soft); }
  .learn-more {
    display: inline-flex; align-items: center; gap: 4px;
    margin-top: 2px; font-size: 10px; color: var(--brand);
  }
  .learn-more::after {
    content: ""; width: 8px; height: 8px; border-radius: 50%;
    background: var(--brand);
  }

  /* Hero band (pre / recovery) */
  .hero {
    position: absolute; left: 0; right: 0; top: 0;
    background: linear-gradient(160deg, var(--brand-soft), var(--brand) 50%, var(--brand-deep));
  }
  .screen--pre .hero { height: 230px; border-radius: 0 0 40px 40px; }
  .screen--recovery .hero { height: 270px; border-radius: 0 0 60px 60px; }
  .screen > * { position: relative; }
  .screen > .hero { position: absolute; }
  .section-title--light { color: #ffffff; }
  .screen--pre .section-title { padding: 30px 22px 20px; }
  .screen--recovery .section-title { text-align: center; padding: 36px 0 22px; }

  /* Accordion */
  .steps { flex: 1 1 auto; min-height: 0; padding: 0 12px; display: flex; flex-direction: column; gap: 14px; }
  .step {
    background: var(--card);
    border-radius: 12px;
    padding: 18px 16px;
    box-shadow: 0 2px 10px rgba(30, 60, 90, 0.08);
  }
  .step__head {
    display: flex; justify-content: space-between; align-items: flex-start; gap: 10px;
    font-family: var(--display);
    font-weight: 600; font-size: 14px; line-height: 1.4;
    text-transform: uppercase; letter-spacing: 0.3px;
  }
  .step__toggle { flex: 0 0 11px; height: 11px; border-radius: 50%; background: #cfd5da; margin-top: 3px; }
  .step--open .step__toggle { background: var(--brand); }
  .step__text { font-size: 9.5px; line-height: 1.75; color: var(--ink-soft); margin-top: 8px; }
  .step__text a { color: var(--brand); text-decoration: underline; }

  /* Recovery grid */
  .recovery-grid {
    flex: 1 1 auto; min-height: 0; padding: 0 12px;
    display: grid; grid-template-columns: 1fr 1fr; gap: 12px;
    align-content: start;
  }
  .tile {
    background: var(--card); border-radius: 10px; padding: 6px 6px 10px;
    text-align: center;
    box-shadow: 0 2px 10px rgba(30, 60, 90, 0.10);
  }
  .tile__photo {
    height: 108px; border-radius: 6px;
    background: linear-gradient(140deg, #9fc4d8, #3f86b0 50%, #d9e3ea);
  }
  .tile__rule { width: 40px; height: 2px; background: var(--brand); margin: 10px auto 6px; }
  .tile__title { font-family: var(--display); font-weight: 500; font-size: 14px; line-height: 1.35; }
  .tile__text { font-size: 9.5px; line-height: 1.6; color: var(--ink-soft); margin-top: 4px; padding: 0 4px; }

  /* Bottom nav */
  .tabbar {
    flex: 0 0 52px;
    margin: 12px 10px 12px;
    height: 52px;
    border-radius: 26px;
    background: var(--brand);
    display: flex; justify-content: space-around; align-items: center;
    padding: 0 8px;
  }
  .tab { display: flex; flex-direction: column; align-items: center; gap: 3px; color: #ffffff; font-size: 9.5px; }
  .tab svg { width: 14px; height: 14px; fill: #ffffff; }
</style>
</head>
<body>

<svg width="0" height="0" style="position:absolute">
  <defs>
    <symbol id="icon-home" viewBox="0 0 16 16"><path d="M8 1 1 7.5h2V15h3.7v-4.3h2.6V15H13V7.5h2z"/></symbol>
    <symbol id="icon-team" viewBox="0 0 16 16"><circle cx="8" cy="5" r="2.6"/><circle cx="3" cy="6" r="1.8"/><circle cx="13" cy="6" r="1.8"/><path d="M3.5 14c0-3 2-4.8 4.5-4.8s4.5 1.8 4.5 4.8z"/><path d="M0 13c0-2 1.2-3.4 3-3.4.7 0 1.2.2 1.6.5C3.8 11 3.2 12 3 13z"/><path d="M16 13c0-2-1.2-3.4-3-3.4-.7 0-1.2.2-1.6.5.8.9 1.4 1.9 1.6 2.9z"/></symbol>
    <symbol id="icon-prev" viewBox="0 0 16 16"><circle cx="8" cy="8" r="7.5"/><path d="M9.5 4 5.5 8l4 4" stroke="#2f86b8" stroke-width="2" fill="none"/></symbol>
    <symbol id="icon-next" viewBox="0 0 16 16"><circle cx="8" cy="8" r="7.5"/><path d="M6.5 4l4 4-4 4" stroke="#2f86b8" stroke-width="2" fill="none"/></symbol>
    <symbol id="icon-gear" viewBox="0 0 16 16"><circle cx="8" cy="8" r="5" fill="none" stroke="#fff" stroke-width="4.5" stroke-dasharray="2.4 1.5"/><circle cx="8" cy="8" r="4.2"/><circle cx="8" cy="8" r="1.8" fill="#2f86b8"/></symbol>
  </defs>
</svg>

<!-- About procedure -->
<section class="screen screen--about">
  <div class="brand"><span class="brand__dot"></span>CareSteps</div>
  <h2 class="section-title">About Procedure</h2>
  <div class="topic-list">
    <article class="topic">
      <div class="topic__photo" role="img" aria-label="Photo of a doctor talking with a patient"></div>
      <div class="topic__body">
        <h3 class="topic__title">Is it too late to prevent gallbladder disease?</h3>
        <p class="topic__text">Yes, unfortunately. If you have symptomatic gallbladder disease, surgery is the most likely solution.</p>
        <span class="learn-more">Learn More</span>
      </div>
    </article>
    <article class="topic">
      <div class="topic__photo" role="img" aria-label="Photo of a nurse helping an older patient in a wheelchair"></div>
      <div class="topic__body">
        <h3 class="topic__title">What will happen if I don't have this procedure?</h3>
        <p class="topic__text">If you chose not to undergo surgery – and do not adopt other solutions - it is likely that your pain will persist.</p>
        <span class="learn-more">Learn More</span>
      </div>
    </article>
    <article class="topic">
      <div class="topic__photo" role="img" aria-label="Photo of a physician consulting with a patient"></div>
      <div class="topic__body">
        <h3 class="topic__title">Are there alternative solutions?</h3>
        <p class="topic__text">If you are suffering from gallbladder disease and are a strong surgical candidate, you should</p>
        <span class="learn-more">Learn More</span>
      </div>
    </article>
    <article class="topic">
      <div class="topic__photo" role="img" aria-label="Photo of a doctor reviewing results with a patient"></div>
      <div class="topic__body">
        <h3 class="topic__title">What are the risks of this procedure?</h3>
        <p class="topic__text">All procedures have risks, but this is usually a straightforward procedure. Serious risks</p>
        <span class="learn-more">Learn More</span>
      </div>
    </article>
  </div>
  <nav class="tabbar">
    <span class="tab"><svg><use href="#icon-home"/></svg>Contents</span>
    <span class="tab"><svg><use href="#icon-team"/></svg>Your Team</span>
    <span class="tab"><svg><use href="#icon-prev"/></svg>Pervious</span>
    <span class="tab"><svg><use href="#icon-next"/></svg>Next</span>
    <span class="tab"><svg><use href="#icon-gear"/></svg>Settings</span>
  </nav>
</section>

<!-- Pre-procedure -->
<section class="screen screen--pre">
  <div class="hero" role="img" aria-label="Blue-toned photo of a doctor with a patient"></div>
  <div class="brand brand--light"><span class="brand__dot"></span>CareSteps</div>
  <h2 class="section-title section-title--light">Pre-Procedure</h2>
  <div class="steps">
    <div class="step"><div class="step__head">Pre-operative appointment<span class="step__toggle"></span></div></div>
    <div class="step step--open">
      <div class="step__head">8 weeks before (or after your pre-operative appointment)<span class="step__toggle"></span></div>
      <p class="step__text">You PCP or GYN may advise that you Stop taking estrogen-containing medications (e.g. hormone replacement therapy or oral contraceptives). Some hormones can increase your risk of blood clots. If you require another form of birth control, discuss this with your primary care physician or GYN.. <a>Learn More</a></p>
    </div>
    <div class="step"><div class="step__head">6 week before<span class="step__toggle"></span></div></div>
    <div class="step"><div class="step__head">2 week before<span class="step__toggle"></span></div></div>
    <div class="step"><div class="step__head">1 week before<span class="step__toggle"></span></div></div>
  </div>
  <nav class="tabbar">
    <span class="tab"><svg><use href="#icon-home"/></svg>Contents</span>
    <span class="tab"><svg><use href="#icon-team"/></svg>Your Team</span>
    <span class="tab"><svg><use href="#icon-prev"/></svg>Pervious</span>
    <span class="tab"><svg><use href="#icon-next"/></svg>Next</span>
    <span class="tab"><svg><use href="#icon-gear"/></svg>Settings</span>
  </nav>
</section>

<!-- Recovery -->
<section class="screen screen--recovery">
  <div class="hero" role="img" aria-label="Blue-toned photo of a nurse caring for a patient"></div>
  <div class="brand brand--light"><span class="brand__dot"></span>CareSteps</div>
  <h2 class="section-title section-title--light">Recovery</h2>
  <div class="recovery-grid">
    <article class="tile">
      <div class="tile__photo" role="img" aria-label="Photo of a nurse with an older patient outdoors"></div>
      <div class="tile__rule"></div>
      <h3 class="tile__title">When do I leave the Hospital?</h3>
      <p class="tile__text">The recovery process is typically uncomplicated and straightforward.</p>
      <span class="learn-more">Learn More</span>
    </article>
    <article class="tile">
      <div class="tile__photo" role="img" aria-label="Photo of a nurse beside a patient in a hospital bed"></div>
      <div class="tile__rule"></div>
      <h3 class="tile__title">Waking up</h3>
      <p class="tile__text">When you wake up and start to remember events, you will be in the post-anesthesia care</p>
      <span class="learn-more">Learn More</span>
    </article>
    <article class="tile">
      <div class="tile__photo" role="img" aria-label="Photo of a doctor reviewing notes with a patient"></div>
      <div class="tile__rule"></div>
      <h3 class="tile__title">Pain management</h3>
      <p class="tile__text">You will slowly experience some pain. Again, this is normal since you just had surgery.</p>
    </article>
    <article class="tile">
      <div class="tile__photo" role="img" aria-label="Photo of a nurse talking with a patient in bed"></div>
      <div class="tile__rule"></div>
      <h3 class="tile__title">Same-day Discharge</h3>
      <p class="tile__text">Once the anesthesia wears off, a few of your friends and family members.</p>
    </article>
  </div>
  <nav class="tabbar">
    <span class="tab"><svg><use href="#icon-home"/></svg>Contents</span>
    <span class="tab"><svg><use href="#icon-team"/></svg>Your Team</span>
    <span class="tab"><svg><use href="#icon-prev"/></svg>Pervious</span>
    <span class="tab"><svg><use href="#icon-next"/></svg>Next</span>
    <span class="tab"><svg><use href="#icon-gear"/></svg>Settings</span>
  </nav>
</section>

</body>
</html>
```